Sales/Landing Page Redesign for Hunting product

I am looking for a redesign for https://ridgelynoutfitters.com/quarter-pad .

We want to add in the information for our new XL quarterpad found: https://ridgelynoutfitters.com/shop/hunting/xl-big-game-quarter-pad/

We also will be adding a spot for this video: https://www.vidstreamhub.com/watch?v=Zk4TnaR8wqe

We like having the 3 options at the bottom, but the goal for this page is to sell the quarter pad.

Target Market(s)

Western Hunters, campers, outdoorsmen

Industry/Entity Type

Hunting

Number of Pages Required

1 page

Font styles to use
Sans Serif

Requirements
Must have
• a clean design that is geared to sell the product.

```html
<!DOCTYPE html>
<html lang="en">
<head>
<meta charset="utf-8">
<title>Ridgelyn Quarter Pads</title>
<link href="https://fonts.googleapis.com/css2?family=Michroma&family=Arimo:ital,wght@0,400;0,700;1,400&family=Caveat:wght@500&display=swap" rel="stylesheet">
<style>
:root{
  --ink:#050b14;
  --navy:#0f1820;
  --navy-2:#1e262f;
  --red:#d01414;
  --red-bright:#ff1a1a;
  --orange:#f07a1c;
  --white:#ffffff;
  --light:#efefef;
}
*{box-sizing:border-box;margin:0;padding:0}
html,body{width:1200px;height:3309px;overflow:hidden;background:var(--white)}
body{position:relative;font-family:"Arimo",Arial,sans-serif;color:var(--ink)}
.abs{position:absolute}
.display{font-family:"Michroma",Arial,sans-serif;text-transform:uppercase;letter-spacing:.5px}
.btn{position:absolute;display:flex;align-items:center;justify-content:center;font:700 8px "Arimo",Arial,sans-serif;text-transform:uppercase;color:var(--white);background:var(--red);box-shadow:0 6px 10px rgba(0,0,0,.25)}
.btn.ghost{background:rgba(0,0,0,.45);border:2px solid var(--red);box-shadow:none}

/* nav */
.nav{left:0;top:0;width:1200px;height:75px;background:var(--ink)}
.brand{font-family:"Michroma",Arial,sans-serif;font-size:12px;color:var(--white);letter-spacing:1px}
.nav .brand{left:24px;top:30px}
.nav-link{font-size:9px;letter-spacing:3px;color:#c9ccd1;text-transform:uppercase}
.nav-pill{left:914px;top:26px;width:118px;height:22px;border-radius:11px;background:#1c2530;display:flex;align-items:center;justify-content:center}
.nav-shop{left:1043px;top:22px;width:88px;height:30px;background:var(--red-bright);color:var(--white);font-size:10px;letter-spacing:2px;display:flex;align-items:center;justify-content:center;font-weight:700}
.cart{left:1145px;top:20px;width:33px;height:33px;border-radius:50%;background:#3a3f46}

/* hero */
.hero{left:0;top:75px;width:1200px;height:424px;
  background:
    radial-gradient(ellipse 38% 34% at 47% 52%,#4d4a4e 0%,rgba(77,74,78,.6) 45%,rgba(77,74,78,0) 100%),
    radial-gradient(ellipse 52% 48% at 42% 45%,#ff9a2a 0%,#f07a1c 40%,#c85a14 65%,rgba(150,110,70,0) 100%),
    linear-gradient(180deg,#8c8470 0%,#7a6a52 40%,#8a6a3c 75%,#6b5a44 100%)}
.hero-title{left:0;top:156px;width:1200px;text-align:center;font-size:22px;color:var(--white);text-shadow:0 2px 6px rgba(0,0,0,.55)}
.hero-sub{left:428px;top:195px;width:340px;height:24px;border-radius:12px;background:rgba(255,255,255,.85);font-style:italic;font-size:13px;display:flex;align-items:center;justify-content:center}
.watch{left:0;top:384px;width:1200px;text-align:center;font-family:"Caveat",cursive;font-size:16px;color:var(--white)}

/* video */
.brush{left:262px;top:499px;width:676px;height:278px;
  background:linear-gradient(90deg,rgba(255,255,255,0) 0%,#c9c9c9 10%,#9a9a9a 30%,#9a9a9a 70%,#c9c9c9 90%,rgba(255,255,255,0) 100%);
  -webkit-mask:linear-gradient(180deg,#000 0%,#000 80%,transparent 100%);mask:linear-gradient(180deg,#000 0%,#000 80%,transparent 100%)}
.video{left:348px;top:456px;width:504px;height:285px;
  background:
    radial-gradient(ellipse 22% 40% at 58% 60%,#7a5a4a 0%,#3a302c 60%,rgba(40,34,30,0) 100%),
    linear-gradient(90deg,#5a3e2a 0%,#4a3322 45%,#3a2a20 62%,#b08a3a 78%,#c89a40 100%);box-shadow:0 6px 18px rgba(0,0,0,.3)}
.video-bar{left:354px;top:715px;width:492px;height:3px;background:#777}
.video-progress{left:354px;top:715px;width:427px;height:3px;background:#e62117}
.video-time{left:431px;top:724px;font-size:8px;color:var(--white)}

/* still cards */
.card{position:absolute;width:225px;height:124px;background:var(--navy)}
.card .thumb{position:absolute;left:18px;top:18px;width:87px;height:87px}
.card p{position:absolute;left:125px;top:50%;transform:translateY(-50%);width:82px;font-style:italic;font-size:13px;line-height:22px;color:var(--white)}
.card p b{font-weight:400;color:var(--red)}
.still-mark{left:478px;top:828px;width:244px;text-align:center;font-family:"Michroma",Arial,sans-serif;font-size:34px;color:#ececec;letter-spacing:1px}
.still-title{left:484px;top:848px;width:232px;text-align:center;font-size:21px;line-height:28px;color:var(--ink)}
.better{left:0;top:1141px;width:1200px;text-align:center;font-size:14px}

/* responsible */
.resp{left:0;top:1279px;width:1200px;height:561px;
  background:
    radial-gradient(ellipse 20% 45% at 50% 48%,#ee8a3c 0%,#d0702c 45%,rgba(150,100,60,.4) 80%,rgba(60,60,50,0) 100%),
    radial-gradient(ellipse 60% 70% at 50% 50%,#4a4a3e 0%,#343a30 60%,#2a2e28 100%)}
.resp-title{left:0;top:1348px;width:1200px;text-align:center;font-size:21px;line-height:31px;color:var(--white);text-shadow:0 2px 6px rgba(0,0,0,.5)}
.feat{position:absolute;width:230px;height:60px;display:flex;align-items:center;background:linear-gradient(90deg,rgba(20,24,28,.9),rgba(20,24,28,.6) 75%,rgba(20,24,28,0))}
.feat svg{margin-left:22px;flex:none}
.feat span{margin-left:16px;font-style:italic;font-size:13px;line-height:22px;color:var(--white)}

/* testimonial */
.testi-title{left:0;top:1910px;width:1200px;text-align:center;font-size:21px;line-height:28px}
.testi-bg{left:0;top:2040px;width:1200px;height:245px;
  background:linear-gradient(180deg,#ffffff 0%,#dfe2e8 25%,#aab2c2 45%,#8a7a78 62%,#5a4a4a 78%,#2a2f3c 100%)}
.quote-brush{left:300px;top:1985px;width:600px;height:222px;background:linear-gradient(90deg,rgba(150,150,150,0),#a0a0a0 8%,#a0a0a0 92%,rgba(150,150,150,0))}
.quote-card{left:329px;top:1997px;width:542px;height:198px;background:var(--navy)}
.quote-text{left:415px;top:2027px;width:372px;text-align:center;font-style:italic;font-size:13px;line-height:22.5px;color:var(--white)}
.quote-name{left:0;top:2137px;width:1200px;text-align:center;font-size:12px;font-weight:700;color:var(--red);letter-spacing:.5px}
.quote-role{left:0;top:2155px;width:1200px;text-align:center;font-size:9px;color:#4a525c}
.qmark{font-family:Georgia,serif;font-size:140px;color:#2a323c;line-height:1}

/* quality */
.quality{left:0;top:2285px;width:1200px;height:308px;
  background:
    radial-gradient(ellipse 7% 15% at 61% 57%,#ff8a2a 0%,#f07a1c 55%,rgba(240,122,28,0) 100%),
    radial-gradient(ellipse 20% 60% at 78% 45%,#5c4a44 0%,#3a3640 55%,rgba(30,38,52,0) 100%),
    linear-gradient(90deg,#1b2433,#1d2736 55%,#232634)}
.quality-title{left:245px;top:2346px;font-size:18px;color:var(--white)}
.quality-title span{color:var(--red)}
.quality-text{left:245px;top:2391px;width:382px;font-size:11px;line-height:22.5px;color:#b8bcc3}

/* products */
.choose-title{left:0;top:2663px;width:1200px;text-align:center;font-size:21px;line-height:28px}
.prod-img{position:absolute;width:220px;height:201px}
.prod-name{position:absolute;width:220px;text-align:center;font-size:11px;font-weight:700;color:var(--red);letter-spacing:.5px}
.prod-price{position:absolute;width:220px;text-align:center;font-style:italic;font-size:18px;color:#333}
.feature-card{left:484px;top:2750px;width:232px;height:321px;background:var(--navy-2);box-shadow:0 10px 25px rgba(0,0,0,.35)}

/* footer */
.footer{left:0;top:3146px;width:1200px;height:163px;background:var(--ink)}
.copy{left:0;top:3226px;width:1200px;text-align:center;font-size:7px;letter-spacing:2px;color:#555c66}
.links{left:0;top:3249px;width:1200px;text-align:center;font-size:9px;color:#7a1515}
.links span{margin:0 10px}
</style>
</head>
<body>

<header class="abs nav">
  <div class="abs brand">RIDGELYN</div>
  <div class="abs nav-link" style="left:856px;top:33px">Meals</div>
  <div class="abs nav-pill"><span class="nav-link">Quarter Pads</span></div>
  <div class="abs nav-shop">SHOP NOW</div>
  <div class="abs cart"></div>
  <svg class="abs" style="left:1154px;top:29px" width="16" height="16" viewBox="0 0 16 16"><path d="M1 2h2l2 8h8l2-6H4" fill="none" stroke="#1a1d22" stroke-width="1.6"/><circle cx="6" cy="13" r="1.3" fill="#1a1d22"/><circle cx="12" cy="13" r="1.3" fill="#1a1d22"/></svg>
</header>

<section class="abs hero" role="img" aria-label="Field-dressed game quarters laid on an orange quarter pad on frosty grass"></section>
<h1 class="abs display hero-title">Quarter Pads to Keep Your Meat Clean</h1>
<div class="abs hero-sub">100% Waterproof • Lightweight • Quality Guarantee</div>
<div class="btn ghost" style="left:499px;top:281px;width:87px;height:29px">Learn More</div>
<div class="btn" style="left:613px;top:281px;width:87px;height:29px">Buy Now</div>
<div class="abs watch">Watch Video</div>
<svg class="abs" style="left:590px;top:408px" width="20" height="32" viewBox="0 0 20 32"><path d="M10 2c4 6-6 10 0 26M4 22l6 8 6-8" fill="none" stroke="#fff" stroke-width="1.8"/></svg>

<div class="abs brush"></div>
<div class="abs video" role="img" aria-label="Product video on VidStreamHub: presenter in a cap explaining the quarter pad"></div>
<div class="abs video-bar"></div>
<div class="abs video-progress"></div>
<svg class="abs" style="left:364px;top:722px" width="60" height="12" viewBox="0 0 60 12"><path d="M2 1l8 5-8 5z" fill="#fff"/><path d="M24 2l6 4-6 4zM31 2v8" fill="#fff" stroke="#fff"/><path d="M45 4h3l3-3v10l-3-3h-3z" fill="#fff"/></svg>
<div class="abs video-time">1:13 / 1:24</div>
<svg class="abs" style="left:736px;top:723px" width="100" height="10" viewBox="0 0 100 10"><rect x="0" y="1" width="11" height="8" fill="none" stroke="#fff"/><circle cx="27" cy="5" r="4" fill="#fff"/><rect x="44" y="1" width="11" height="8" fill="none" stroke="#fff"/><rect x="66" y="2" width="11" height="6" fill="none" stroke="#fff"/><path d="M88 1h-2v3M96 1h2v3M88 9h-2V6M96 9h2V6" fill="none" stroke="#fff"/></svg>

<div class="abs still-mark">RIDGELYN</div>
<div class="card" style="left:231px;top:806px"><div class="thumb" style="background:linear-gradient(135deg,#7a6a4a,#c89a80 55%,#8a7a5a)" role="img" aria-label="Fresh meat lying on a rock"></div><p>Lay your fresh meat on a rock<b>?</b></p></div>
<div class="card" style="left:744px;top:806px"><div class="thumb" style="background:linear-gradient(160deg,#1a6a9a,#38a8d8 60%,#2a7aaa)" role="img" aria-label="Blue tarp shelter"></div><p>Use a blue tarp<b>?</b></p></div>
<div class="card" style="left:244px;top:950px"><div class="thumb" style="background:linear-gradient(135deg,#e8d8d0,#c8585a 45%,#5a4030)" role="img" aria-label="Raw meat on dirt"></div><p>Lay your meat on the dirt<b>?</b></p></div>
<div class="card" style="left:488px;top:980px"><div class="thumb" style="background:linear-gradient(135deg,#1a2a4a,#2a3a6a 60%,#3a2a3a)" role="img" aria-label="Hands sewing bed sheets"></div><p>Sew beds sheets together<b>?</b></p></div>
<div class="card" style="left:731px;top:950px"><div class="thumb" style="background:linear-gradient(90deg,#6a1a1a,#3a2a2a 35%,#d88a8a 70%,#f0e0e0)" role="img" aria-label="Meat stuffed in an old pillow case"></div><p>Stuff meat in used old pillow cases<b>?</b></p></div>

<h2 class="abs display still-title">Do You<br>...Still...</h2>
<h3 class="abs display better">There is a Better Way</h3>
<div class="btn" style="left:524px;top:1173px;width:152px;height:30px">Select My Quarter Pad</div>

<section class="abs resp" role="img" aria-label="Overhead view of a hunter laying game quarters on an orange quarter pad"></section>
<h2 class="abs display resp-title">Be Responsible.<br>Use a Quarterpad.</h2>

<div class="feat" style="left:250px;top:1449px"><svg width="30" height="30" viewBox="0 0 30 30"><circle cx="15" cy="15" r="14" fill="var(--red)"/><path d="M9 15l4 4 8-9" fill="none" stroke="#fff" stroke-width="2.5"/></svg><span>Keep your meat<br>off the dirt</span></div>
<div class="feat" style="left:250px;top:1548px"><svg width="30" height="30" viewBox="0 0 30 30"><circle cx="15" cy="15" r="14" fill="var(--red)"/><path d="M9 15l4 4 8-9" fill="none" stroke="#fff" stroke-width="2.5"/></svg><span>Lightweight</span></div>
<div class="feat" style="left:250px;top:1648px"><svg width="30" height="30" viewBox="0 0 30 30"><circle cx="15" cy="15" r="14" fill="var(--red)"/><path d="M9 15l4 4 8-9" fill="none" stroke="#fff" stroke-width="2.5"/></svg><span>100%<br>Water proof</span></div>
<div class="feat" style="left:740px;top:1449px"><svg width="30" height="30" viewBox="0 0 30 30"><circle cx="15" cy="15" r="14" fill="var(--red)"/><path d="M9 15l4 4 8-9" fill="none" stroke="#fff" stroke-width="2.5"/></svg><span>Reusable</span></div>
<div class="feat" style="left:740px;top:1548px"><svg width="30" height="30" viewBox="0 0 30 30"><circle cx="15" cy="15" r="14" fill="var(--red)"/><path d="M9 15l4 4 8-9" fill="none" stroke="#fff" stroke-width="2.5"/></svg><span>55” x 60”<br>when open</span></div>
<div class="feat" style="left:740px;top:1640px;height:76px"><svg width="30" height="30" viewBox="0 0 30 30"><circle cx="15" cy="15" r="14" fill="var(--red)"/><path d="M9 15l4 4 8-9" fill="none" stroke="#fff" stroke-width="2.5"/></svg><span>Respect the animal<br>by keeping it<br>contamination free</span></div>
<div class="btn" style="left:524px;top:1735px;width:152px;height:31px">Select My Quarter Pad</div>

<h2 class="abs display testi-title">What Others<br>Are Saying</h2>
<div class="abs testi-bg" role="img" aria-label="Desert mountain range at dusk"></div>
<div class="abs quote-brush"></div>
<div class="abs quote-card"></div>
<div class="abs qmark" style="left:338px;top:1985px">“</div>
<div class="abs qmark" style="left:770px;top:2100px">”</div>
<p class="abs quote-text">The Quarter Pads keep your meat clean and double up as a waterproof poncho and ground tarp. They are a must have for any serious hunter.</p>
<div class="abs quote-name">WADE HARLAN</div>
<div class="abs quote-role">Hunter</div>
<svg class="abs" style="left:248px;top:2082px" width="38" height="28" viewBox="0 0 38 28"><path d="M36 14H3M14 3L3 14l11 11" fill="none" stroke="var(--red)" stroke-width="2"/></svg>
<svg class="abs" style="left:913px;top:2082px" width="38" height="28" viewBox="0 0 38 28"><path d="M2 14h33M24 3l11 11-11 11" fill="none" stroke="var(--red)" stroke-width="2"/></svg>

<section class="abs quality" role="img" aria-label="Presenter holding a packed orange quarter pad"></section>
<h2 class="abs display quality-title"><span>100%</span> Quality Guaranteed</h2>
<p class="abs quality-text">We've designed our Quarter Pads for maximum performance and durability so you can keep the meat you harvest in the backcountry clean and out of the dirt. If you are at all unsatisfied, contact us and we'll make it right.</p>
<div class="btn" style="left:245px;top:2486px;width:152px;height:31px">Contact Us Now</div>

<h2 class="abs display choose-title">Choose Your<br>Quarter Pad</h2>

<div class="prod-img" style="left:234px;top:2761px;background:radial-gradient(ellipse 30% 36% at 50% 50%,#c21d1d 0%,#c21d1d 70%,var(--light) 100%)" role="img" aria-label="Red quarter pad stuff sack"></div>
<div class="prod-name" style="left:234px;top:2974px">RED QUARTER PAD</div>
<div class="prod-price" style="left:234px;top:2994px">$19.99</div>
<div class="btn" style="left:299px;top:3024px;width:88px;height:28px">Buy Now</div>

<div class="abs feature-card"></div>
<div class="prod-img" style="left:490px;top:2756px;width:220px;height:200px;background:radial-gradient(ellipse 28% 34% at 50% 48%,var(--orange) 0%,var(--orange) 70%,var(--navy-2) 100%)" role="img" aria-label="Orange quarter pad stuff sack"></div>
<div class="prod-name" style="left:490px;top:2971px">ORANGE QUARTER PAD</div>
<div class="prod-price" style="left:490px;top:2990px;color:var(--white)">$19.99 / <span style="font-size:12px">XL $29.99</span></div>
<div class="btn ghost" style="left:512px;top:3024px;width:88px;height:28px;background:transparent">Buy Now</div>
<div class="btn" style="left:600px;top:3024px;width:88px;height:28px">Buy XL Now</div>

<div class="prod-img" style="left:747px;top:2761px;background:radial-gradient(ellipse 30% 36% at 50% 48%,#1fa85a 0%,#1fa85a 70%,var(--light) 100%)" role="img" aria-label="Green quarter pad stuff sack"></div>
<div class="prod-name" style="left:747px;top:2974px">GREEN QUARTER PAD</div>
<div class="prod-price" style="left:747px;top:2994px">$19.99</div>
<div class="btn" style="left:812px;top:3024px;width:88px;height:28px">Buy Now</div>

<footer class="abs footer"></footer>
<div class="abs brand" style="left:0;width:1200px;text-align:center;top:3184px">RIDGELYN</div>
<div class="abs" style="left:580px;top:3206px;width:12px;height:12px;border-radius:50%;background:#fff"></div>
<div class="abs" style="left:608px;top:3206px;width:12px;height:12px;border-radius:50%;background:#fff"></div>
<div class="abs copy">COPYRIGHT © 2020</div>
<div class="abs links"><span>My Account</span><span>Blog</span><span>Terms of Service Agreement</span><span>Refund and Return Policy</span><span>Privacy Policy Agreement</span></div>

</body>
</html>
```